New Webpage for High Class Expert Witness Services Company

We are looking for a minimalist design for a webpage that just has our logo and an entry form offer to connect with one of our Liaisons.
The entry form should just ask for Name, Email, Contact Info and Description of Project.

Company Name is: The Marlowe Crest Advisory Services

Number of Pages Required

1 page

```html
<!DOCTYPE html>
<html lang="en">
<head>
<meta charset="utf-8">
<title>The Marlowe Crest Advisory Services — Contact</title>
<link rel="stylesheet" href="https://fonts.googleapis.com/css2?family=Cinzel:wght@500;600;700&family=Poppins:wght@400;500;600&display=swap">
<style>
  :root{
    --ink:#262626;
    --panel:#2b2b2b;
    --photo-dark:#1f2224;
    --photo-mid:#4a5154;
    --photo-light:#7d8588;
    --copper:#a86f40;
    --card:#e6e6e7;
    --field-line:#8d8d8d;
    --label:#3a3a3a;
    --white:#ffffff;
    --soft-white:rgba(255,255,255,.88);
  }
  *{margin:0;padding:0;box-sizing:border-box}
  html,body{width:1200px;height:675px;overflow:hidden;background:var(--panel)}
  .page{position:relative;width:1200px;height:675px;overflow:hidden;font-family:"Poppins",sans-serif}

  .hero-photo{
    position:absolute;left:0;top:0;width:862px;height:675px;
    background:
      linear-gradient(90deg,rgba(20,20,20,.85) 0%,rgba(20,20,20,.55) 45%,rgba(20,20,20,.15) 100%),
      radial-gradient(ellipse at 62% 40%,var(--photo-light) 0%,var(--photo-mid) 40%,var(--photo-dark) 100%);
  }
  .side-panel{position:absolute;left:862px;top:0;width:338px;height:675px;background:var(--panel);border-left:1px solid rgba(255,255,255,.35)}
  .side-word{
    position:absolute;left:1108px;top:-4px;
    writing-mode:vertical-rl;
    font-family:"Cinzel",serif;font-weight:500;font-size:124px;letter-spacing:2px;
    color:rgba(255,255,255,.06);line-height:1;white-space:nowrap;
  }

  .brand{position:absolute;left:112px;top:24px;display:flex;align-items:center;gap:10px}
  .brand-mark{width:22px;height:22px;border:2px solid var(--white)}
  .brand-text{display:flex;flex-direction:column;gap:3px}
  .brand-name{font-family:"Cinzel",serif;font-weight:600;font-size:17px;color:var(--white);letter-spacing:.5px;line-height:1}
  .brand-tagline{font-family:"Cinzel",serif;font-weight:500;font-size:6.5px;color:var(--soft-white);letter-spacing:2px}

  .hero-title{
    position:absolute;left:112px;top:240px;width:470px;
    font-family:"Cinzel",serif;font-weight:700;font-size:46px;line-height:57px;
    color:var(--white);letter-spacing:1.5px;
  }
  .hero-lede{
    position:absolute;left:112px;top:421px;width:380px;
    font-size:13px;line-height:21px;color:var(--soft-white);font-weight:400;
  }
  .legal{position:absolute;left:112px;top:625px;font-size:9.3px;color:rgba(255,255,255,.8);font-weight:500}

  .contact-card{position:absolute;left:731px;top:141px;width:363px;height:400px;background:var(--card)}
  .contact-card header{
    height:57px;background:var(--copper);display:flex;align-items:center;justify-content:center;
    font-family:"Cinzel",serif;font-weight:600;font-size:17px;color:var(--white);letter-spacing:.5px;
  }
  .contact-form{position:absolute;left:21px;top:86px;width:319px}
  .field{
    display:block;width:318px;height:36px;margin-bottom:7px;
    border:1px solid var(--field-line);background:transparent;
    font-family:"Poppins",sans-serif;font-size:10.5px;color:var(--label);
    padding:10px 12px 0;
  }
  .field::placeholder{color:var(--label)}
  textarea.field{height:103px;resize:none;padding-top:9px;margin-bottom:19px}
  .submit{
    display:block;width:317px;height:39px;margin-left:1px;border:0;background:var(--ink);
    color:var(--white);font-family:"Poppins",sans-serif;font-weight:600;font-size:11px;letter-spacing:.3px;cursor:pointer;
  }
</style>
</head>
<body>
<main class="page">
  <div class="hero-photo" role="img" aria-label="Photo of a smiling professional in a grey blazer holding a tablet on a balcony in front of a modern apartment building"></div>
  <aside class="side-panel"></aside>
  <div class="side-word" aria-hidden="true">MARLOWE</div>

  <div class="brand">
    <span class="brand-mark"></span>
    <div class="brand-text">
      <span class="brand-name">The Marlowe Crest Advisory Services</span>
      <span class="brand-tagline">SEAMLESS MEDICAL EXPERT INTEGRATION</span>
    </div>
  </div>

  <h1 class="hero-title">THE MARLOWE CREST ADVISORY SERVICES</h1>
  <p class="hero-lede">Connect with a dedicated Liaison to discuss your project securely and&nbsp; confidentially.</p>
  <p class="legal">© The Marlowe Crest Advisory Services | All inquiries are handled with strict confidentiality.</p>

  <section class="contact-card">
    <header>CONTACT OUR DEFENSE LIAISONS</header>
    <form class="contact-form">
      <input class="field" type="text" placeholder="Name*">
      <input class="field" type="email" placeholder="Email*">
      <input class="field" type="tel" placeholder="Phone*">
      <textarea class="field" placeholder="Project Description*"></textarea>
      <button class="submit" type="button">SUBMIT</button>
    </form>
  </section>
</main>
</body>
</html>
```